Executive Business Card for Healthcare Company [Need Today]

I need a business card design for a healthcare company. The only branding the company has thus far is a logo. The cards will be utilized by company executives. The design I envision will be vibrant and appealing but with a corporate feel. They shouldn't be too casual or playful. I would like to complete this project TODAY if possible.

Target Market(s)

Healthcare vendors, other executives in healthcare and pharmaceuticals

Industry/Entity Type

Pharmaceutical

Contact Information for Business Card

See attachment

Font styles to use
Serif
Sans Serif

Colors

Designer to choose colors to be used in the design.

```html
<!DOCTYPE html>
<html lang="en">
<head>
<meta charset="utf-8">
<title>Corvale Therapeutics – Business Card</title>
<link rel="stylesheet" href="https://fonts.googleapis.com/css2?family=Work+Sans:wght@400;500;700&display=swap">
<style>
  :root {
    --backdrop: #d7dbdb;
    --paper: #f3f2ee;
    --forest: #1f2c28;
    --teal: #1fa7a2;
    --teal-soft: #3dbba3;
    --ink: #2b2f30;
    --paper-edge: #c9cbc6;
  }
  * { margin: 0; padding: 0; box-sizing: border-box; }
  html, body {
    width: 1200px; height: 900px; overflow: hidden;
    background: var(--backdrop);
    font-family: "Work Sans", Arial, sans-serif;
  }
  .canvas {
    position: relative; width: 1200px; height: 900px;
    display: flex; flex-direction: column; align-items: center; justify-content: center; gap: 56px;
  }
  .card {
    width: 600px; height: 343px; position: relative;
    box-shadow: 0 6px 18px rgba(0,0,0,.12);
  }
  .card--front { background: var(--paper); border: 1px solid var(--paper-edge); }
  .card--back { background: var(--forest); display: flex; align-items: center; justify-content: center; }

  .brand { display: flex; align-items: center; gap: 12px; }
  .brand__mark {
    border: 2px solid var(--teal-soft); border-radius: 50%; flex: none;
  }
  .brand__name { color: var(--teal); font-weight: 500; line-height: 1.05; }

  .card--front .brand { position: absolute; left: 42px; top: 118px; }
  .card--front .brand__mark { width: 62px; height: 62px; }
  .card--front .brand__name { font-size: 21px; }

  .card--back .brand { gap: 18px; }
  .card--back .brand__mark { width: 104px; height: 104px; }
  .card--back .brand__name { font-size: 34px; }

  .divider {
    position: absolute; left: 292px; top: 58px; width: 3px; height: 226px; background: var(--teal);
  }
  .contact { position: absolute; left: 318px; top: 62px; color: var(--ink); }
  .contact__name { color: var(--teal); font-weight: 700; font-size: 25px; line-height: 1.1; }
  .contact__title { font-size: 14px; margin-top: 4px; }
  .contact__address { font-size: 14px; line-height: 1.4; margin-top: 12px; font-style: normal; }
  .contact__list { list-style: none; margin-top: 12px; font-size: 14px; line-height: 1.5; }
  .contact__item { display: flex; align-items: center; gap: 9px; }
  .contact__icon { width: 12px; height: 12px; flex: none; }
</style>
</head>
<body>
<main class="canvas">
  <section class="card card--front" aria-label="Business card front">
    <div class="brand">
      <span class="brand__mark"></span>
      <span class="brand__name">Corvale<br>Therapeutics</span>
    </div>
    <span class="divider"></span>
    <div class="contact">
      <h1 class="contact__name">Daniel Marsh</h1>
      <p class="contact__title">Senior Director of Marketing</p>
      <address class="contact__address">
        Corvale Therapeutics, LLC<br>
        118 W Laurel Avenue<br>
        Marion, GA 30412
      </address>
      <ul class="contact__list">
        <li class="contact__item">
          <svg class="contact__icon" viewBox="0 0 12 12" aria-hidden="true"><path d="M2.5 1 L4.5 1 L5.3 3.4 L4 4.4 Q5 6.8 7.6 8 L8.6 6.7 L11 7.5 L11 9.5 Q10.6 11 9 11 Q1 10 1 2.6 Q1 1.2 2.5 1Z" fill="var(--teal)"/></svg>
          555-210-4837
        </li>
        <li class="contact__item">
          <svg class="contact__icon" viewBox="0 0 12 12" aria-hidden="true"><rect x="3" y="0.8" width="6" height="10.4" rx="1" fill="none" stroke="var(--teal)" stroke-width="1.4"/><circle cx="6" cy="9.2" r=".7" fill="var(--teal)"/></svg>
          555-390-2615
        </li>
        <li class="contact__item">
          <svg class="contact__icon" viewBox="0 0 12 12" aria-hidden="true"><rect x="0.8" y="2.3" width="10.4" height="7.4" rx="1" fill="none" stroke="var(--teal)" stroke-width="1.4"/><path d="M1 3 L6 6.6 L11 3" fill="none" stroke="var(--teal)" stroke-width="1.2"/></svg>
          dmarsh@corvalerx.com
        </li>
      </ul>
    </div>
  </section>

  <section class="card card--back" aria-label="Business card back">
    <div class="brand">
      <span class="brand__mark"></span>
      <span class="brand__name">Corvale<br>Therapeutics</span>
    </div>
  </section>
</main>
</body>
</html>
```